Corvane Capital Business Cards

These are professional business cards that are for my family office.
Put fake emails and phone numbers as of now until I finalize those components. This family office controls my families investments, assets, and future. The cards should be professional.
..
.
.
.
I just uploaded another variation of a logo I would like to see as a business card to I am inbeteen which logo to use

Target Market(s)

business

Industry/Entity Type

business

Contact Information for Business Card

Professional, wealth related, finance related.

Requirements
Must have
• Logo

```html
<!DOCTYPE html>
<html lang="en">
<head>
<meta charset="UTF-8">
<title>Corvane Capital Business Cards</title>
<link rel="stylesheet" href="https://fonts.googleapis.com/css2?family=Playfair+Display:wght@500;600&family=Poppins:wght@400&display=swap">
<style>
  :root {
    --backdrop: #bdbdbd;
    --navy-deep: #000c1f;
    --navy-ring: #1e2a42;
    --navy-ink: #1a2338;
    --paper-light: #f7f7f7;
    --paper-mid: #e9e9e9;
    --ring-grey: #c4c4c4;
    --white: #ffffff;
    --text-grey: #2a2a2a;
  }
  * { margin: 0; padding: 0; box-sizing: border-box; }
  html, body {
    width: 975px; height: 1200px; overflow: hidden;
    background: var(--backdrop);
  }
  .canvas { position: relative; width: 975px; height: 1200px; }
  .card {
    position: absolute; left: 91px; width: 805px; height: 459px;
    overflow: hidden;
    box-shadow: 12px 14px 14px rgba(0,0,0,0.28);
  }
  .card-front { top: 112px; background: var(--navy-deep); }
  .card-back {
    top: 635px;
    background: radial-gradient(ellipse at 40% 45%, var(--paper-light) 0%, var(--paper-mid) 100%);
  }
  .card-decor { position: absolute; inset: 0; }

  .brand-mark { position: absolute; text-align: center; transform: translateX(-50%); }
  .brand-circle { display: block; margin: 0 auto; border-radius: 50%; }
  .brand-name {
    display: block; white-space: nowrap;
    font-family: 'Playfair Display', serif; font-weight: 500;
    text-transform: uppercase; letter-spacing: 1.5px;
  }
  .card-front .brand-mark { left: 403px; top: 103px; }
  .card-front .brand-circle { width: 138px; height: 138px; border: 3px solid var(--white); }
  .card-front .brand-name { color: var(--white); font-size: 27px; margin-top: 14px; }

  .front-url {
    position: absolute; left: 0; right: 0; top: 336px; text-align: center;
    font-family: 'Poppins', sans-serif; font-size: 25px; letter-spacing: 3.4px;
    color: var(--white);
  }

  .card-back .brand-mark { left: 615px; top: 231px; }
  .card-back .brand-circle { width: 112px; height: 112px; border: 2.5px solid var(--navy-ink); }
  .card-back .brand-name { color: var(--navy-ink); font-size: 22px; margin-top: 13px; }

  .holder { position: absolute; left: 71px; top: 168px; }
  .holder-name {
    font-family: 'Playfair Display', serif; font-weight: 600;
    font-size: 46px; line-height: 1.1; color: var(--navy-ink); letter-spacing: 0.5px;
  }
  .holder-role {
    font-family: 'Poppins', sans-serif; font-size: 20px; color: var(--text-grey);
    margin-top: 2px;
  }
  .contact-list { position: absolute; left: 69px; top: 286px; list-style: none; }
  .contact-item {
    display: flex; align-items: center; height: 33.5px;
    font-family: 'Poppins', sans-serif; font-size: 17.5px; color: var(--text-grey);
  }
  .contact-icon { width: 22px; height: 22px; margin-right: 10px; flex: none; }
</style>
</head>
<body>
<div class="canvas">

  <section class="card card-front">
    <svg class="card-decor" width="805" height="459" viewBox="0 0 805 459">
      <g fill="none" stroke="var(--navy-ring)">
        <circle cx="26" cy="23" r="107" stroke-width="32"/>
        <circle cx="26" cy="23" r="67" stroke-width="18"/>
        <circle cx="776" cy="461" r="106" stroke-width="46"/>
        <circle cx="776" cy="461" r="70" stroke-width="16"/>
      </g>
    </svg>
    <div class="brand-mark">
      <span class="brand-circle"></span>
      <span class="brand-name">Corvane Capital</span>
    </div>
    <p class="front-url">www.corvanecapital.com</p>
  </section>

  <section class="card card-back">
    <svg class="card-decor" width="805" height="459" viewBox="0 0 805 459">
      <circle cx="744" cy="92" r="138" fill="none" stroke="var(--navy-ink)" stroke-width="40"/>
      <circle cx="744" cy="92" r="110" fill="var(--white)"/>
      <circle cx="744" cy="92" r="86" fill="none" stroke="var(--ring-grey)" stroke-width="24"/>
    </svg>

    <div class="holder">
      <h1 class="holder-name">ELIAS MARLOW</h1>
      <p class="holder-role">Company CEO</p>
    </div>

    <ul class="contact-list">
      <li class="contact-item">
        <svg class="contact-icon" viewBox="0 0 22 22">
          <circle cx="11" cy="11" r="11" fill="var(--navy-ink)"/>
          <path d="M7.2 6.2c.5-.4 1.1-.3 1.4.2l1 1.6c.3.5.2 1-.2 1.3l-.6.5c.5 1.2 1.5 2.2 2.7 2.8l.5-.6c.3-.4.9-.5 1.3-.2l1.6 1c.5.3.6.9.2 1.4l-.6.7c-.6.6-1.6.8-2.4.4-2.5-1.2-4.4-3.1-5.6-5.6-.4-.8-.2-1.8.4-2.4z" fill="var(--white)"/>
        </svg>
        014.2873.560
      </li>
      <li class="contact-item">
        <svg class="contact-icon" viewBox="0 0 22 22">
          <circle cx="11" cy="11" r="11" fill="var(--navy-ink)"/>
          <rect x="5.5" y="7" width="11" height="8" rx="1" fill="var(--white)"/>
          <path d="M5.8 7.5l5.2 4 5.2-4" fill="none" stroke="var(--navy-ink)" stroke-width="1.1"/>
        </svg>
        office@corvanecapital.com
      </li>
      <li class="contact-item">
        <svg class="contact-icon" viewBox="0 0 22 22">
          <circle cx="11" cy="11" r="11" fill="var(--navy-ink)"/>
          <g fill="none" stroke="var(--white)" stroke-width="1">
            <circle cx="11" cy="11" r="5.5"/>
            <ellipse cx="11" cy="11" rx="2.4" ry="5.5"/>
            <path d="M5.5 11h11M6.3 8.2h9.4M6.3 13.8h9.4"/>
          </g>
        </svg>
        www.corvanecapital.com
      </li>
    </ul>

    <div class="brand-mark">
      <span class="brand-circle"></span>
      <span class="brand-name">Corvane Capital</span>
    </div>
  </section>

</div>
</body>
</html>
```